Canadian Christian Church needs design for new sermon series

A graphic design for our series and an invitation card to invite people to the series. Check design brief for more detailed information. Target audience: young families and young adults. Looking for a creative design that will get people's attention and create interest. See design brief for copy of design purchased for previous series.
Updates
entered Apr 4 incorrectly. Need a week to receive and review designs, and today is Apr 2/19. Thanks!
Target Market(s)
young families and young adults
Colors
Designer to choose colors to be used in the design.
Look and feel

```html
<!DOCTYPE html>
<html lang="en">
<head>
<meta charset="utf-8">
<title>Messy – Sermon Series Invitation Card</title>
<link href="https://fonts.googleapis.com/css2?family=Anton&family=Arvo:wght@400;700&family=Montserrat:wght@400;600&family=Open+Sans:wght@400&family=Roboto+Slab:wght@300;400;700&display=swap" rel="stylesheet">
<style>
  :root{
    --backdrop:#e4e4e4;
    --band:#3d3431;
    --ink:#3a3330;
    --orange:#f7941d;
    --orange-light:#ffc14d;
    --purple:#6b2a7a;
    --violet:#8a2a8f;
    --blue:#1f7fc4;
    --beige-1:#d8cfb8;
    --beige-2:#c6bb9f;
    --tick:#1f7fc4;
  }
  *{margin:0;padding:0;box-sizing:border-box}
  html,body{width:1200px;height:903px;overflow:hidden;background:var(--backdrop)}
  .canvas{position:relative;width:1200px;height:903px}

  .card{position:absolute;width:482px;height:378px;overflow:hidden;box-shadow:0 2px 6px rgba(0,0,0,.18)}

  /* Front */
  .card--front{left:177px;top:61px}
  .front__photo{position:absolute;inset:0 0 42px 0;
    background:linear-gradient(160deg,#c9b89a 0%,#a88f6c 35%,#4a3a30 65%,#8b8174 100%)}
  .front__title{position:absolute;left:35px;top:22px;font-family:'Anton',sans-serif;font-size:70px;line-height:1;letter-spacing:1px;
    background:linear-gradient(180deg,var(--orange-light),var(--orange) 60%,#e0671a);-webkit-background-clip:text;background-clip:text;color:transparent;
    -webkit-text-stroke:2px var(--purple)}
  .front__church{position:absolute;left:295px;top:30px;width:160px;display:flex;flex-direction:column;align-items:center;gap:6px;
    font-family:'Roboto Slab','Arvo',serif;font-weight:300;font-size:12.5px;color:var(--ink);white-space:nowrap}
  .front__church-dot{width:60px;height:60px;border-radius:50%;background:var(--purple)}
  .front__tagline{position:absolute;left:0;right:0;top:350px;transform:translateY(-64px);text-align:center;font-family:'Roboto Slab','Arvo',serif;font-weight:400;font-size:34px;line-height:1;
    color:var(--orange);-webkit-text-stroke:1px #3a2410;letter-spacing:-.3px;text-shadow:1px 2px 3px rgba(0,0,0,.5)}
  .front__band{position:absolute;left:0;right:0;bottom:0;height:42px;background:var(--band);color:#fff;
    font-family:'Roboto Slab','Arvo',serif;font-weight:300;font-size:22px;display:flex;align-items:center;justify-content:center}

  /* Back */
  .card--back{left:582px;top:470px;background:linear-gradient(135deg,var(--beige-1),var(--beige-2));color:var(--ink)}
  .back__heading{position:absolute;left:0;right:0;top:24px;text-align:center;font-family:'Roboto Slab','Arvo',serif;font-weight:700;line-height:1.25}
  .back__heading h1{font-size:26px;font-weight:700;letter-spacing:-.3px}
  .back__heading p{font-size:26px;font-weight:700}
  .back__section{position:absolute;left:26px;font-family:'Montserrat',sans-serif}
  .back__section h2{font-size:12px;font-weight:600;margin-bottom:3px}
  .back__list{list-style:none}
  .back__list li{font-size:11.2px;line-height:14.6px;display:flex;align-items:center;gap:6px;white-space:nowrap}
  .back__list li b{font-weight:600}
  .tick{width:8px;height:8px;flex:none}
  .back__sermons{top:106px}
  .back__features{top:255px}
  .back__values{position:absolute;left:288px;top:101px;width:176px;height:176px}
  .values__name{font-family:'Montserrat',sans-serif;font-size:6.2px;font-weight:600;fill:#fff;letter-spacing:.2px}
  .values__note{font-family:'Montserrat',sans-serif;font-size:3.6px;fill:#fff}
  .values__core{font-family:'Montserrat',sans-serif;font-size:8px;font-weight:600;fill:var(--ink)}
  .back__footer{position:absolute;left:0;right:0;bottom:0;height:56px;background:var(--band);color:#fff;
    font-family:'Open Sans',sans-serif;font-size:10.5px;padding:10px 28px 0 28px;display:flex;justify-content:space-between}
  .footer__row{display:flex;align-items:center;gap:4px;line-height:16px}
  .footer__row svg{width:9px;height:9px;flex:none}
  .footer__email{color:var(--orange)}
</style>
</head>
<body>
<main class="canvas">

  <section class="card card--front">
    <div class="front__photo" role="img" aria-label="Photograph of a cluttered home office desk covered in papers"></div>
    <div class="front__title">MESSY</div>
    <div class="front__church"><span class="front__church-dot"></span><span>Maple Ridge Family Church</span></div>
    <div class="front__tagline">Joining God in the Mess</div>
    <div class="front__band">Connecting Young Families to Christ</div>
  </section>

  <section class="card card--back">
    <div class="back__heading">
      <h1>THE TIME OF THE SERVICES:</h1>
      <p>Sundays @ 10:30</p>
    </div>

    <div class="back__section back__sermons">
      <h2>Names &amp; Dates of the sermons:</h2>
      <ul class="back__list">
        <li><svg class="tick" viewBox="0 0 8 8"><circle cx="4" cy="4" r="4" fill="var(--tick)"/><path d="M2.2 4.1l1.2 1.2 2.4-2.5" stroke="#fff" stroke-width="1" fill="none"/></svg><span><b>April 28th:</b> “We Made This Mess”</span></li>
        <li><svg class="tick" viewBox="0 0 8 8"><circle cx="4" cy="4" r="4" fill="var(--tick)"/><path d="M2.2 4.1l1.2 1.2 2.4-2.5" stroke="#fff" stroke-width="1" fill="none"/></svg><span><b>May 5th:</b> “Bless in the Mess”</span></li>
        <li><svg class="tick" viewBox="0 0 8 8"><circle cx="4" cy="4" r="4" fill="var(--tick)"/><path d="M2.2 4.1l1.2 1.2 2.4-2.5" stroke="#fff" stroke-width="1" fill="none"/></svg><span><b>May 12th:</b> “Born into the Mess”</span></li>
        <li><svg class="tick" viewBox="0 0 8 8"><circle cx="4" cy="4" r="4" fill="var(--tick)"/><path d="M2.2 4.1l1.2 1.2 2.4-2.5" stroke="#fff" stroke-width="1" fill="none"/></svg><span><b>May 19th:</b> “Messy Work”</span></li>
        <li><svg class="tick" viewBox="0 0 8 8"><circle cx="4" cy="4" r="4" fill="var(--tick)"/><path d="M2.2 4.1l1.2 1.2 2.4-2.5" stroke="#fff" stroke-width="1" fill="none"/></svg><span><b>May 26th:</b> “Messy Church”</span></li>
        <li><svg class="tick" viewBox="0 0 8 8"><circle cx="4" cy="4" r="4" fill="var(--tick)"/><path d="M2.2 4.1l1.2 1.2 2.4-2.5" stroke="#fff" stroke-width="1" fill="none"/></svg><span><b>June 2nd:</b> “Messy Hospitality”</span></li>
        <li><svg class="tick" viewBox="0 0 8 8"><circle cx="4" cy="4" r="4" fill="var(--tick)"/><path d="M2.2 4.1l1.2 1.2 2.4-2.5" stroke="#fff" stroke-width="1" fill="none"/></svg><span><b>June 9th:</b> TBD</span></li>
        <li><svg class="tick" viewBox="0 0 8 8"><circle cx="4" cy="4" r="4" fill="var(--tick)"/><path d="M2.2 4.1l1.2 1.2 2.4-2.5" stroke="#fff" stroke-width="1" fill="none"/></svg><span><b>June 16th:</b> “Messy within Boundaries”</span></li>
      </ul>
    </div>

    <svg class="back__values" viewBox="0 0 180 180" role="img" aria-label="Core values ring: equipping, serving, missional living, spirit-living and belonging">
      <g fill="none" stroke-width="34">
        <circle cx="90" cy="90" r="66" stroke="var(--orange)" stroke-dasharray="80 334.7" transform="rotate(-160 90 90)"/>
        <circle cx="90" cy="90" r="66" stroke="var(--blue)" stroke-dasharray="80 334.7" transform="rotate(-88 90 90)"/>
        <circle cx="90" cy="90" r="66" stroke="var(--orange)" stroke-dasharray="80 334.7" transform="rotate(-16 90 90)"/>
        <circle cx="90" cy="90" r="66" stroke="var(--violet)" stroke-dasharray="80 334.7" transform="rotate(56 90 90)"/>
        <circle cx="90" cy="90" r="66" stroke="var(--blue)" stroke-dasharray="80 334.7" transform="rotate(128 90 90)"/>
      </g>
      <g text-anchor="middle">
        <text class="values__core" x="90" y="88">CORE</text>
        <text class="values__core" x="90" y="97">VALUES</text>

        <text class="values__name" x="51" y="34">EQUIPPING</text>
        <text class="values__note" x="51" y="40">preparing our people</text>
        <text class="values__note" x="51" y="44.5">to further the kingdom</text>

        <text class="values__name" x="129" y="34">SERVING</text>
        <text class="values__note" x="129" y="40">generously giving our</text>
        <text class="values__note" x="129" y="44.5">time, talent, and treasure</text>

        <text class="values__name" x="153" y="104">MISSIONAL</text>
        <text class="values__name" x="153" y="111">LIVING</text>
        <text class="values__note" x="153" y="117">intentionally pursuing</text>
        <text class="values__note" x="153" y="121.5">the lost where they are</text>

        <text class="values__name" x="90" y="152">SPIRIT-LIVING</text>
        <text class="values__note" x="90" y="158">being led, transformed, and</text>
        <text class="values__note" x="90" y="162.5">empowered by the Holy Spirit</text>

        <text class="values__name" x="27" y="107">BELONGING</text>
        <text class="values__note" x="27" y="113">nurturing a family</text>
        <text class="values__note" x="27" y="117.5">environment</text>
      </g>
    </svg>

    <div class="back__section back__features">
      <h2>Features of the service:</h2>
      <ul class="back__list">
        <li><svg class="tick" viewBox="0 0 8 8"><circle cx="4" cy="4" r="4" fill="var(--tick)"/><path d="M2.2 4.1l1.2 1.2 2.4-2.5" stroke="#fff" stroke-width="1" fill="none"/></svg><span>Staffed nursery &amp; children’s program every Sunday</span></li>
        <li><svg class="tick" viewBox="0 0 8 8"><circle cx="4" cy="4" r="4" fill="var(--tick)"/><path d="M2.2 4.1l1.2 1.2 2.4-2.5" stroke="#fff" stroke-width="1" fill="none"/></svg><span>Coffee &amp; snacks</span></li>
        <li><svg class="tick" viewBox="0 0 8 8"><circle cx="4" cy="4" r="4" fill="var(--tick)"/><path d="M2.2 4.1l1.2 1.2 2.4-2.5" stroke="#fff" stroke-width="1" fill="none"/></svg><span>Everyone welcome</span></li>
      </ul>
    </div>

    <footer class="back__footer">
      <div>
        <div class="footer__row"><svg viewBox="0 0 10 10"><path d="M5 .5a3.3 3.3 0 0 0-3.3 3.3C1.7 6.3 5 9.5 5 9.5s3.3-3.2 3.3-5.7A3.3 3.3 0 0 0 5 .5z" fill="none" stroke="var(--orange)" stroke-width="1.2"/><circle cx="5" cy="3.8" r="1.1" fill="var(--orange)"/></svg>1185 Harbour Line East Oakfield, ON L6R 2T4</div>
        <div class="footer__row"><svg viewBox="0 0 10 10"><path d="M2.2 1l1.6 1.9-.9 1.3a6 6 0 0 0 2.9 2.9l1.3-.9L9 7.8 8 9C4.4 8.8 1.2 5.6 1 2z" fill="var(--orange)"/></svg>905-555-0142 &nbsp;&nbsp;&nbsp;<svg viewBox="0 0 10 10"><circle cx="5" cy="5" r="4.2" fill="none" stroke="var(--orange)" stroke-width="1"/><path d="M.8 5h8.4M5 .8c-2.2 2.4-2.2 6 0 8.4M5 .8c2.2 2.4 2.2 6 0 8.4" stroke="var(--orange)" stroke-width=".8" fill="none"/></svg>www.mrfamilychurch.ca</div>
      </div>
      <div>
        <div class="footer__row">Please contact Laura Pennington</div>
        <div class="footer__row footer__email">worship@mrfamilychurch.ca</div>
      </div>
    </footer>
  </section>

</main>
</body>
</html>
```